Create the ONLY Supplement line for Male Entrepreneurs! (Verity Nine MD)

I need a label designed for a new supplement brand that I am launching.

There are five products so need a design that I can simply change the wording for each individual product

The brand name is called verity nine MD. The focus is male entrepreneurial health.

Target audience is men 35 to 55.

Concepts: the healthier you are in body the more money you will make in business.

Concept to copy: I want to make a clean minimalistic label mimicking Lansworth MD (google it and you'll see what I mean)

Target Market(s)

male entrepreneurs 35-55

Industry/Entity Type

Health Supplement

Colors

Designer to choose colors to be used in the design.

Requirements
Must have
• Modern classy design, similar to Lansworth MD.
Nice to have
• Highlight that the supplement is Doctor Approved.
Should not have
• No loud colors. Present it as high class.

```html
<!DOCTYPE html>
<html lang="en">
<head>
<meta charset="utf-8">
<title>Verity Nine MD – NVx for Men Label Set</title>
<link href="https://fonts.googleapis.com/css2?family=Fira+Sans:wght@300;400;500&display=swap" rel="stylesheet">
<style>
  :root {
    --canvas: #f1f1f1;
    --paper: #ffffff;
    --stage: #e3e3e3;
    --green: #00a97f;
    --green-soft: #2fae8a;
    --brown: #5c2d00;
    --olive: #7d6500;
    --ink: #4a4a4a;
    --rule: #5a3a2a;
    --frame: #9a9a9a;
  }
  * { margin: 0; padding: 0; box-sizing: border-box; }
  html, body { width: 1200px; height: 716px; overflow: hidden; }
  body {
    background: var(--canvas);
    position: relative;
    font-family: "Fira Sans", Arial, sans-serif;
    font-weight: 300;
    color: var(--ink);
  }
  .label, .stage, .label-front { position: absolute; background: var(--paper); }
  .label { border: 1px solid var(--frame); }
  .stage { background: var(--stage); left: 847px; top: 75px; width: 297px; height: 559px; }
  .label-front { left: 76px; top: 92px; width: 181px; height: 380px; background: linear-gradient(160deg, #f7f7f7, #ececec); }
  .t { position: absolute; line-height: 1; white-space: nowrap; }
  .body-copy { letter-spacing: 0.3px; }
  .brand { font-weight: 500; color: var(--green); }
  .rule { position: absolute; height: 1px; background: var(--rule); }
  .band { position: absolute; background: var(--green); color: #fff; }
  .band .t { color: #fff; font-weight: 400; }
  .mark { position: absolute; display: flex; align-items: center; gap: 4px; font-weight: 500; color: var(--green); line-height: 1; white-space: nowrap; }
  .mark i { display: block; border-radius: 50%; background: currentColor; }

  .label--brown .brand { color: var(--brown); }
  .label--brown .olive { color: var(--olive); }
  .label--brown .mark { color: var(--brown); }
  .label--brown .band { background: var(--brown); }
</style>
</head>
<body>

<!-- Tall label -->
<section class="label" style="left:79px;top:75px;width:280px;height:559px;">
  <div class="t brand" style="left:20px;top:31px;font-size:26.5px;">Verity Nine MD</div>
  <div class="rule" style="left:20px;top:63px;width:236px;"></div>
  <div class="t body-copy" style="left:20px;top:69px;font-size:16px;">NVx for Men</div>
  <div class="mark" style="left:10px;top:413px;font-size:13px;"><i style="width:12px;height:12px;"></i>Verity Nine</div>
  <div class="t body-copy" style="left:10px;top:438px;font-size:16px;">Lightweight Moisturizer</div>
  <div class="t body-copy" style="left:10px;top:456px;font-size:16px;">Soin Hydratant Fluide</div>
  <div class="band" style="left:-1px;top:481px;width:257px;height:38px;">
    <div class="t" style="left:13px;top:11px;font-size:16px;">Supplement is Doctor Approved</div>
  </div>
  <div class="t body-copy" style="left:10px;top:524px;font-size:16px;">e59ml / 2fl oz</div>
</section>

<!-- Wide label, green -->
<section class="label" style="left:433px;top:75px;width:344px;height:200px;">
  <div class="t brand" style="left:10px;top:22px;font-size:24px;">Verity Nine MD</div>
  <div class="rule" style="left:10px;top:47px;width:225px;"></div>
  <div class="t body-copy" style="left:10px;top:52px;font-size:15px;">NVx for Men</div>
  <div class="mark" style="left:10px;top:108px;font-size:12px;"><i style="width:11px;height:11px;"></i>Verity Nine</div>
  <div class="t body-copy" style="left:10px;top:128px;font-size:15px;">Lightweight Moisturizer</div>
  <div class="t body-copy" style="left:10px;top:145px;font-size:15px;">Soin Hydratant Fluide</div>
  <div class="t body-copy" style="right:15px;top:145px;font-size:15px;">e59ml / 2fl oz</div>
  <div class="band" style="left:-1px;top:165px;width:345px;height:35px;">
    <div class="t" style="left:12px;top:10px;font-size:15px;">Supplement is Doctor Approved</div>
  </div>
</section>

<!-- Wide label, brown -->
<section class="label label--brown" style="left:433px;top:302px;width:335px;height:334px;">
  <div class="t brand" style="left:10px;top:16px;font-size:24px;">Verity Nine MD</div>
  <div class="rule" style="left:10px;top:42px;width:225px;"></div>
  <div class="t body-copy olive" style="left:10px;top:47px;font-size:15px;">NVx for Men</div>
  <div class="mark" style="left:10px;top:242px;font-size:12px;"><i style="width:11px;height:11px;"></i>Verity Nine</div>
  <div class="t body-copy olive" style="left:10px;top:262px;font-size:15px;">Lightweight Moisturizer</div>
  <div class="t body-copy olive" style="left:10px;top:279px;font-size:15px;">Soin Hydratant Fluide</div>
  <div class="t body-copy olive" style="right:12px;top:279px;font-size:15px;">e59ml / 2fl oz</div>
  <div class="band" style="left:-1px;top:299px;width:336px;height:34px;">
    <div class="t" style="left:12px;top:10px;font-size:15px;">Supplement is Doctor Approved</div>
  </div>
</section>

<!-- Flat front panel on grey ground -->
<section class="stage">
  <div class="label-front">
    <div class="t brand" style="left:14px;top:115px;font-size:16px;color:var(--green-soft);top:117px;"></div>
    <div class="t brand" style="left:14px;top:117px;font-size:16px;color:var(--green-soft);display:none;"></div>
    <div class="t brand" style="left:14px;top:25px;font-size:16px;font-weight:400;color:var(--green-soft);">Verity Nine MD</div>
    <div class="rule" style="left:14px;top:43px;width:153px;"></div>
    <div class="t body-copy" style="left:14px;top:47px;font-size:10px;">NVx for Men</div>
    <div class="mark" style="left:7px;top:279px;font-size:9px;color:var(--green-soft);"><i style="width:8px;height:8px;"></i>Verity Nine</div>
    <div class="t body-copy" style="left:7px;top:298px;font-size:10px;">Lightweight Moisturizer</div>
    <div class="t body-copy" style="left:7px;top:310px;font-size:10px;">Soin Hydratant Fluide</div>
    <div class="band" style="left:0;top:326px;width:167px;height:26px;background:var(--green-soft);">
      <div class="t" style="left:8px;top:9px;font-size:10px;font-weight:300;">Supplement is Doctor Approved</div>
    </div>
    <div class="t body-copy" style="left:7px;top:357px;font-size:10px;">e59ml / 2fl oz</div>
  </div>
</section>

</body>
</html>
```